VELMOR Website Design

We need a website designed for our company VELMOR. We are a luxury lifestyle club that will provide benefits and services for our members. The site should be clean & sleek, preferably using black and white (or darker colors). (example sites: stravenhall.example, plinth.example)

Here is a link of a sample page I did using wix. (https://dunmere7.sitehostly.example/mysite) This can be used to get a general idea.

Target Market(s)

Upper Middle Class in the United States

Number of Pages Required

5+ page

Font styles to use
Sans Serif
Other font styles liked:
• Arial (or other similar fonts)

Requirements
Must have
• A clean design that is eye-catching and speaks to our company.
Nice to have
• Ideas for copy.

```html
<!DOCTYPE html>
<html lang="en">
<head>
<meta charset="utf-8">
<title>VELMOR — Exclusive Lifestyle Club</title>
<link rel="stylesheet" href="https://fonts.googleapis.com/css2?family=Montserrat:wght@300;400;500;600;700&family=Open+Sans:wght@400;600;700&display=swap">
<style>
  :root{
    --black:#000;
    --ink:#0b0b0b;
    --panel:#111;
    --white:#fff;
    --muted:#c9c9c9;
    --dim:#8d8d8d;
    --gold:#e6b93b;
    --gold-dark:#c99a22;
    --star:#f05a28;
    --line:#2a2a2a;
  }
  *{box-sizing:border-box;margin:0;padding:0}
  html,body{width:1200px;height:3435px;overflow:hidden;background:var(--black)}
  body{position:relative;font-family:"Open Sans",Arial,sans-serif;color:var(--white)}
  .abs{position:absolute}

  /* hero */
  .hero{left:0;top:0;width:1200px;height:832px;
    background:radial-gradient(ellipse at 45% 20%,#6a5a7a 0%,#3a3040 30%,#1a1618 60%,#0a0a0a 100%)}
  .hero-shade{left:0;top:0;width:1200px;height:832px;
    background:linear-gradient(180deg,rgba(0,0,0,.35) 0%,rgba(0,0,0,.1) 35%,rgba(0,0,0,.75) 70%,#0d0d0d 100%)}
  .nav a{position:absolute;top:90px;font-family:"Montserrat",Arial,sans-serif;font-size:13px;color:var(--white);text-decoration:none}
  .logo{font-family:"Montserrat",Arial,sans-serif;font-weight:400;color:var(--white);letter-spacing:2px}
  .nav .logo{position:absolute;left:600px;top:76px;transform:translateX(-50%);font-size:32px}
  .menu-icon{left:1038px;top:90px}
  .play{left:568px;top:449px}
  .hero-title{left:0;top:536px;width:1200px;text-align:center;font-family:"Open Sans",Arial,sans-serif;font-weight:700;font-size:60px;line-height:74px}
  .hero-title .accent{color:var(--gold)}
  .search{left:176px;top:737px;width:850px;height:44px;background:var(--white);border:2px solid #bdbdbd;display:flex}
  .search .field{flex:0 0 auto;height:100%;display:flex;align-items:center;padding-left:22px;font-size:15px;color:#8a8a8a}
  .search .find{width:338px;border-right:1px solid #cfcfcf}
  .search .near{width:256px}
  .search .cta{flex:1;background:var(--gold);color:#111;font-family:"Montserrat",Arial,sans-serif;font-weight:600;font-size:15px;display:flex;align-items:center;justify-content:center}

  /* welcome */
  .welcome-title{left:165px;top:920px;font-family:"Montserrat",Arial,sans-serif;font-weight:400;font-size:38px;line-height:52px}
  .welcome-title strong{font-weight:600;font-size:48px;display:block}
  .divider-v{left:506px;top:870px;width:1px;height:282px;background:#3a3a3a}
  .welcome-copy{left:556px;top:864px;width:450px;font-size:14px;line-height:29.5px;color:var(--muted)}
  .btn{display:flex;align-items:center;justify-content:center;background:var(--gold);color:#111;border-radius:22px;font-family:"Montserrat",Arial,sans-serif;font-weight:500;font-size:14px}
  .read-more{left:554px;top:1127px;width:128px;height:43px}
  .rule{left:0;top:1230px;width:1200px;height:1px;background:var(--line)}

  /* explore */
  .section-title{left:0;width:1200px;text-align:center;font-family:"Montserrat",Arial,sans-serif;font-weight:400;font-size:30px}
  .explore-title{top:1296px}
  .explore-sub{left:0;top:1370px;width:1200px;text-align:center;font-size:13px;line-height:22px;color:var(--white)}
  .photo{position:absolute}
  .p-stage{left:0;top:1491px;width:598px;height:547px;background:radial-gradient(ellipse at 55% 35%,#5a5e66 0%,#2a2e36 45%,#0c0d10 100%)}
  .p-pair{left:600px;top:1491px;width:300px;height:275px;background:linear-gradient(135deg,#6c8fb4 0%,#9fb7cc 45%,#d9d4cb 100%)}
  .p-sea{left:900px;top:1766px;width:300px;height:272px;background:linear-gradient(180deg,#2e8aa8 0%,#1d6a86 50%,#0f3d52 100%)}
  .p-confetti{left:0;top:2040px;width:598px;height:548px;background:radial-gradient(ellipse at 50% 45%,#5a4a48 0%,#2a2224 50%,#0e0c0d 100%)}
  .p-yacht{left:600px;top:2040px;width:600px;height:548px;background:linear-gradient(160deg,#c9ced3 0%,#8a9299 45%,#3e4650 100%)}
  .card{position:absolute;background:var(--black);text-align:center}
  .card h3{font-family:"Montserrat",Arial,sans-serif;font-weight:600;font-size:15px;letter-spacing:.5px}
  .card .stars{color:var(--star);font-size:13px;letter-spacing:2px;margin-top:8px}
  .card .price{font-size:13px;margin-top:8px}
  .card .price b{color:var(--gold);font-size:26px;font-weight:700}
  .card .apply{font-size:13px;margin-top:16px}
  .card-estate{left:900px;top:1491px;width:300px;height:275px;padding-top:68px}
  .card-exp{left:600px;top:1766px;width:300px;height:272px;padding-top:84px}
  .notch{position:absolute}

  .view-more{left:543px;top:2668px;width:128px;height:44px}

  /* why */
  .why-title{top:2793px;font-size:34px}
  .why-rule{left:570px;top:2851px;width:60px;height:3px;background:var(--gold)}
  .feature h4{position:absolute;font-family:"Montserrat",Arial,sans-serif;font-weight:600;font-size:18px}
  .feature p{position:absolute;width:260px;font-size:13.5px;line-height:19px;color:var(--dim)}

  /* footer */
  .footer{left:0;top:3092px;width:1200px;height:343px;border-top:1px solid #1d1d1d;
    background:radial-gradient(ellipse at 50% 0%,#1c1c1c 0%,#0d0d0d 55%,#050505 100%)}
  .footer .logo{position:absolute;left:222px;top:3210px;font-size:38px}
  .socials{left:212px;top:3270px;display:flex;gap:10px}
  .socials span{width:30px;height:30px;border:2px solid var(--white);border-radius:50%}
  .footer-mail{left:196px;top:3314px;font-size:13px}
  .fcol h5{position:absolute;font-family:"Montserrat",Arial,sans-serif;font-weight:400;font-size:18px}
  .fcol ul{position:absolute;list-style:none;font-size:12.5px;line-height:23px;color:var(--muted)}
</style>
</head>
<body>

<section class="hero-wrap">
  <div class="abs hero" role="img" aria-label="Photo of a group of friends celebrating at a nightclub under purple stage lights"></div>
  <div class="abs hero-shade"></div>
  <nav class="nav">
    <a href="#" style="left:156px">Reviews</a>
    <a href="#" style="left:245px">About us</a>
    <a href="#" style="left:344px">Mission Planning</a>
    <span class="logo">VELMOR</span>
    <a href="#" style="left:736px">FAQs</a>
    <a href="#" style="left:807px">Donations</a>
    <a href="#" style="left:914px">Sponsors</a>
  </nav>
  <svg class="abs menu-icon" width="20" height="16" viewBox="0 0 20 16" aria-label="Menu"><rect y="1" width="20" height="3" fill="#fff"/><rect y="7" width="20" height="3" fill="#fff"/><rect y="13" width="20" height="3" fill="#fff"/></svg>
  <svg class="abs play" width="64" height="64" viewBox="0 0 64 64" aria-label="Play video"><circle cx="32" cy="32" r="30" fill="rgba(0,0,0,.25)" stroke="#fff" stroke-width="2"/><path d="M26 21 L44 32 L26 43 Z" fill="#fff"/></svg>
  <h1 class="abs hero-title">VELMOR is truly most Exclusive<br><span class="accent">Lifestyle</span> Club</h1>
  <form class="abs search">
    <div class="field find">Find</div>
    <div class="field near">Near</div>
    <div class="cta">Start Pre-Mission Planning</div>
  </form>
</section>

<section class="welcome">
  <h2 class="abs welcome-title">Welcome to <strong>VELMOR</strong></h2>
  <div class="abs divider-v"></div>
  <p class="abs welcome-copy">The website HAS to be interactive, fun, and creative. Nothing animated or clip art style. We want real pictures and videos through-out the entire site. These clips can include but are not limited to a guy setting the hook on a bass, fishing both saltwater and freshwater, hunting both big game and small game to also include aerial hog hunts, jumping out of a plane or the actual sky diving, white water rafting, rock climbing, stunt aircraft rides, hiking, and camping in spots with amazing views.</p>
  <a class="abs btn read-more">Read More</a>
  <div class="abs rule"></div>
</section>

<section class="explore">
  <h2 class="abs section-title explore-title">Explore the Life</h2>
  <p class="abs explore-sub">The website HAS to be interactive, fun, and creative. Nothing<br>animated or clip art style.</p>

  <div class="photo p-stage" role="img" aria-label="Photo of a singer performing on stage before a large crowd"></div>
  <div class="photo p-pair" role="img" aria-label="Photo of a smiling couple outdoors"></div>
  <div class="card card-estate">
    <h3>REAL ESTATE SERVICES</h3>
    <div class="stars">★★★★</div>
    <div class="price">from <b>$335</b>/ 4days 3 Nights</div>
    <div class="apply">Apply now</div>
  </div>
  <svg class="notch" style="left:888px;top:1616px" width="12" height="24" viewBox="0 0 12 24"><path d="M12 0 L0 12 L12 24 Z" fill="#000"/></svg>
  <div class="card card-exp">
    <h3>EXPERIENCES</h3>
    <div class="stars">★★★★</div>
    <div class="price">from <b>$335</b>/ 4days 3 Nights</div>
    <div class="apply">Apply now</div>
  </div>
  <svg class="notch" style="left:900px;top:1890px" width="12" height="24" viewBox="0 0 12 24"><path d="M0 0 L12 12 L0 24 Z" fill="#000"/></svg>
  <div class="photo p-sea" role="img" aria-label="Photo of a diver swimming beside a manta ray"></div>
  <div class="photo p-confetti" role="img" aria-label="Photo of three women blowing confetti at a party"></div>
  <div class="photo p-yacht" role="img" aria-label="Photo of a stylish couple aboard a yacht"></div>

  <a class="abs btn view-more">View More</a>
</section>

<section class="why">
  <h2 class="abs section-title why-title">Why Choose Us</h2>
  <div class="abs why-rule"></div>

  <div class="feature">
    <svg class="abs" style="left:94px;top:2910px" width="44" height="44" viewBox="0 0 44 44" fill="none" stroke="#e6b93b" stroke-width="2"><path d="M8 4 H28 L36 12 V40 H8 Z"/><path d="M14 16 H28 M14 22 H30 M14 28 H24"/><circle cx="32" cy="33" r="6"/><path d="M29 33 L31 35 L35 31"/></svg>
    <h4 style="left:153px;top:2912px">Best Price Guarantee</h4>
    <p style="left:153px;top:2942px">Aliquam vulputate, tortor nec commodo ultricies, lectus nisl facilisis enim, vitae viverra urna nulla&nbsp; turpis.</p>
  </div>
  <div class="feature">
    <svg class="abs" style="left:456px;top:2908px" width="46" height="46" viewBox="0 0 46 46" fill="none" stroke="#e6b93b" stroke-width="2"><circle cx="22" cy="24" r="15"/><path d="M7 24 H37 M22 9 C15 16 15 32 22 39 M22 9 C29 16 29 32 22 39"/><path d="M30 6 L42 4 L36 12 Z" fill="#e6b93b"/></svg>
    <h4 style="left:513px;top:2910px">World Class Service</h4>
    <p style="left:513px;top:2942px">Aliquam vulputate, tortor nec commodo ultricies, lectus nisl facilisis enim, vitae viverra urna nulla&nbsp; turpis.</p>
  </div>
  <div class="feature">
    <svg class="abs" style="left:816px;top:2908px" width="40" height="46" viewBox="0 0 40 46" fill="none" stroke="#e6b93b" stroke-width="2"><circle cx="20" cy="16" r="12"/><path d="M20 9 L22 14 L27 14 L23 17 L25 22 L20 19 L15 22 L17 17 L13 14 L18 14 Z" fill="#e6b93b"/><path d="M12 25 L8 42 L14 38 L17 44 L20 28 M28 25 L32 42 L26 38 L23 44 L20 28"/></svg>
    <h4 style="left:866px;top:2910px">Best Lifestyle Club</h4>
    <p style="left:866px;top:2942px">Aliquam vulputate, tortor nec commodo ultricies, lectus nisl facilisis enim, vitae viverra urna nulla&nbsp; turpis.</p>
  </div>
</section>

<footer>
  <div class="abs footer" role="img" aria-label="Faint dark photo of a crowd behind the footer"></div>
  <span class="logo">VELMOR</span>
  <div class="abs socials"><span></span><span></span><span></span><span></span></div>
  <div class="abs footer-mail">contact@maisonbrisac.example</div>

  <div class="fcol">
    <h5 style="left:440px;top:3218px">A Propos</h5>
    <ul style="left:440px;top:3252px"><li>Notre mission</li><li>Comment camarche ?</li><li>Garanties et SAV</li><li>Espace presse</li></ul>
  </div>
  <div class="fcol">
    <h5 style="left:627px;top:3216px">Travel</h5>
    <ul style="left:627px;top:3246px"><li>Nos artisans</li><li>Vendre sur Maison Brisac</li><li>Blog</li><li>Conditions de vente</li></ul>
  </div>
  <div class="fcol">
    <h5 style="left:834px;top:3213px">Ressources</h5>
    <ul style="left:834px;top:3243px"><li>Questions frequentes</li><li>Vendre sur Maison Brisac</li><li>Blog</li><li>Conditions de vente</li><li>Guides travaux Liens SEO</li></ul>
  </div>
</footer>

</body>
</html>
```